Business cards to launch an education platform

Hi,
I am looking at having new business cards designed.
I am a startup, developing a web platform for schools and university, the education world. It's an online assessment system.
I would like a card that looks classy, and that is using the colors and the font of my logo.

I have attached:
1) my logo
2) A business card that I have designed quickly so you can have all the information required in the card, but I really don't like it.
3) The font that I am using (Lato Regular) to design my web platform
4) Some screenshots of my web platform so you can have a look at the style that I have.

Target Market(s)

Major market: Education system: Schools and university
Minor markets: Business in general

Industry/Entity Type

Business

Contact Information for Business Card

Clara Fenwick
Director

M: 0437 518 902
E: clara.fenwick@amberLoomSystems.com.au

Requirements
Must have
• The colors of my logo

```html
<!DOCTYPE html>
<html lang="en">
<head>
<meta charset="utf-8">
<title>Amber Loom Systems – Business Cards</title>
<link rel="stylesheet" href="https://fonts.googleapis.com/css2?family=Lato:wght@400;700&display=swap">
<style>
  :root {
    --navy: #17416f;
    --sky: #29b5e3;
    --white: #ffffff;
    --backdrop: #ece7df;
    --card-w: 856px;
    --card-h: 487px;
  }
  * { box-sizing: border-box; margin: 0; padding: 0; }
  html, body {
    width: 1189px;
    height: 1200px;
    overflow: hidden;
    background: var(--backdrop);
    font-family: "Lato", Arial, sans-serif;
  }
  .canvas { position: relative; width: 1189px; height: 1200px; }
  .card {
    position: absolute;
    left: 171px;
    width: var(--card-w);
    height: var(--card-h);
    border-radius: 18px;
    overflow: hidden;
  }
  .card--front { top: 68px; background: var(--navy); }
  .card--back { top: 627px; background: var(--white); }

  .brand {
    position: absolute;
    left: 199px;
    display: flex;
    align-items: center;
    gap: 22px;
  }
  .card--front .brand { top: 175px; }
  .card--back .brand { top: 56px; }
  .brand__mark { width: 112px; height: 112px; flex: none; }
  .brand__name {
    font-weight: 400;
    font-size: 48px;
    line-height: 1.05;
    letter-spacing: 0.08em;
    text-transform: uppercase;
  }
  .card--front .brand__mark { background: var(--white); }
  .card--front .brand__name { color: var(--white); }
  .card--back .brand__mark { background: var(--navy); }
  .card--back .brand__name { color: var(--navy); }

  .card__stripe {
    position: absolute;
    left: 0; top: 245px;
    width: 100%; height: 42px;
    background: var(--sky);
  }
  .card__details {
    position: absolute;
    left: 0; top: 287px;
    width: 100%; height: 200px;
    background: var(--navy);
    color: var(--white);
    text-align: center;
  }
  .contact-name { margin-top: 18px; font-weight: 700; font-size: 33px; line-height: 1.1; }
  .contact-role { font-size: 20px; line-height: 1.2; }
  .contact-lines { margin-top: 24px; font-size: 22px; line-height: 1.35; }
  .contact-lines b { font-weight: 700; }
</style>
</head>
<body>
<main class="canvas">
  <section class="card card--front" aria-label="Card front">
    <div class="brand">
      <div class="brand__mark"></div>
      <p class="brand__name">Amber Loom<br>Systems</p>
    </div>
  </section>

  <section class="card card--back" aria-label="Card back">
    <div class="brand">
      <div class="brand__mark"></div>
      <p class="brand__name">Amber Loom<br>Systems</p>
    </div>
    <div class="card__stripe"></div>
    <div class="card__details">
      <p class="contact-name">Clara Fenwick</p>
      <p class="contact-role">Director</p>
      <div class="contact-lines">
        <p><b>M:</b> 0437 518 902</p>
        <p><b>E:</b> clara.fenwick@amberLoomSystems.com.au</p>
      </div>
    </div>
  </section>
</main>
</body>
</html>
```